stationary deign for trucking company

im a trucking company looking for a professional set of stationary designs i deliver goods from point a to b
Updates

When submitting stationary designs I need envelope design, letterhead, cards, I’d badge etc

Industry/Entity Type

Trucking Company

Requirements
Must have
• must have letter head, business card, envelope, fax sheet, id badge, folder, thank you card, notebook, invoice sheet.
Nice to have
• nice to have them all custom made (letterhead,envelope, business card, I’d badge etc
Should not have
• must not have prepaid sign want i unique design for items

```html
<!DOCTYPE html>
<html lang="en">
<head>
<meta charset="utf-8">
<title>Halvern Transportation + Logistics – Business Card</title>
<link rel="stylesheet" href="https://fonts.googleapis.com/css2?family=Montserrat:wght@400;500;600;700&family=Raleway:wght@400;500&display=swap">
<style>
  :root {
    --stage: #1f1f21;
    --card-white: #ffffff;
    --card-black: #1b1b1d;
    --ink: #141414;
    --ink-soft: #4a4a4a;
    --brand-blue: #1d56b8;
    --photo-blue: #6e9ccd;
    --photo-blue-deep: #5a89bd;
  }
  * { box-sizing: border-box; margin: 0; padding: 0; }
  html, body { width: 1200px; height: 1200px; overflow: hidden; }
  body {
    background: var(--stage);
    font-family: "Raleway", Arial, sans-serif;
    position: relative;
  }
  .card {
    position: absolute;
    left: 220px;
    width: 760px;
    height: 434px;
    overflow: hidden;
  }
  .card--front { top: 120px; background: var(--card-white); border-bottom: 7px solid var(--brand-blue); }
  .card--back { top: 646px; background: var(--card-black); border-bottom: 7px solid var(--brand-blue); }

  /* front */
  .portrait {
    position: absolute;
    right: 0; top: 0;
    width: 380px; height: 310px;
    background: linear-gradient(160deg, var(--photo-blue) 0%, var(--photo-blue-deep) 100%);
    clip-path: polygon(30% 0, 100% 0, 100% 100%, 46% 100%, 36% 72%, 12% 50%, 14% 20%);
  }
  .brand {
    position: absolute;
    left: 44px; top: 150px;
    display: flex; align-items: center; gap: 18px;
  }
  .brand__square {
    width: 54px; height: 54px;
    border: 4px solid var(--ink);
    flex: none;
  }
  .brand__name {
    font-family: "Montserrat", Arial, sans-serif;
    font-weight: 600;
    font-size: 52px;
    letter-spacing: 5px;
    color: var(--ink);
    line-height: 1;
  }
  .brand__tagline {
    font-family: "Montserrat", Arial, sans-serif;
    font-weight: 500;
    font-size: 13px;
    letter-spacing: 3.4px;
    color: var(--ink);
    margin-top: 6px;
  }
  .contact {
    position: absolute;
    left: 120px; top: 250px;
  }
  .contact__name {
    font-family: "Montserrat", Arial, sans-serif;
    font-weight: 600;
    font-size: 20px;
    letter-spacing: 1px;
    color: var(--brand-blue);
  }
  .contact__role {
    font-size: 15px;
    color: var(--ink-soft);
    margin-top: 2px;
    margin-bottom: 12px;
  }
  .contact__list { list-style: none; }
  .contact__item {
    display: flex; align-items: center; gap: 12px;
    font-size: 15px; color: var(--ink);
    line-height: 25px;
    white-space: nowrap;
  }
  .contact__item svg { width: 14px; height: 14px; fill: var(--brand-blue); flex: none; }
  .front-tab {
    position: absolute;
    left: 0; bottom: 0;
    width: 34px; height: 14px;
    background: var(--brand-blue);
  }

  /* back */
  .back-pattern {
    position: absolute; inset: 0;
    background: linear-gradient(135deg, #232326 0%, #19191b 100%);
  }
  .back-brand {
    position: absolute;
    right: 120px; top: 180px;
    display: flex; align-items: center; gap: 12px;
  }
  .back-brand__square {
    width: 20px; height: 20px;
    background: var(--brand-blue);
  }
  .back-brand__name {
    font-family: "Montserrat", Arial, sans-serif;
    font-weight: 600;
    font-size: 34px;
    letter-spacing: 3px;
    color: var(--brand-blue);
  }
</style>
</head>
<body>

<section class="card card--front">
  <div class="portrait" role="img" aria-label="Blue-toned portrait photo of the consultant in a suit"></div>

  <div class="brand">
    <div class="brand__square"></div>
    <div>
      <div class="brand__name">HALVERN</div>
      <div class="brand__tagline">TRANSPORTATION + LOGISTICS</div>
    </div>
  </div>

  <div class="contact">
    <div class="contact__name">DANA WHITCOMBE</div>
    <div class="contact__role">Senior Consultant</div>
    <ul class="contact__list">
      <li class="contact__item">
        <svg viewBox="0 0 16 16"><path d="M3.5 1h3l1.5 4-2 1.2a8 8 0 0 0 3.8 3.8L11 8l4 1.5v3A2 2 0 0 1 13 15 12 12 0 0 1 1 3a2 2 0 0 1 2.5-2z"/></svg>
        (402) 555-0148
      </li>
      <li class="contact__item">
        <svg viewBox="0 0 16 16"><path d="M1 3h14v10H1zM2.5 4.5 8 9l5.5-4.5v-.2h-11z" fill-rule="evenodd"/></svg>
        info@halvernfreight.com
      </li>
      <li class="contact__item">
        <svg viewBox="0 0 16 16"><circle cx="8" cy="8" r="7"/><path d="M1 8h14M8 1c-3 3.5-3 10.5 0 14M8 1c3 3.5 3 10.5 0 14" stroke="#fff" stroke-width="1.2" fill="none"/></svg>
        www.halvernfreight.com
      </li>
      <li class="contact__item">
        <svg viewBox="0 0 16 16"><path d="M8 1a5 5 0 0 1 5 5c0 4-5 9-5 9S3 10 3 6a5 5 0 0 1 5-5zm0 3a2 2 0 1 0 0 4 2 2 0 0 0 0-4z" fill-rule="evenodd"/></svg>
        418 Harbor Ave. Ste 210 Marlow, VA 23400
      </li>
    </ul>
  </div>

  <div class="front-tab"></div>
</section>

<section class="card card--back">
  <div class="back-pattern" role="img" aria-label="Black card stock with a repeating embossed brand pattern"></div>
  <div class="back-brand">
    <div class="back-brand__square"></div>
    <div class="back-brand__name">HALVERN</div>
  </div>
</section>

</body>
</html>
```